Casa Morellina Togo Menu seperated in categories

new to go menu for italian restaurant with menu descriptions and prices i like the cover first page to have all the restaurant information, the other pages should be separated in the menu categories, and if we can include a map with the location of the restaurant
Casa Morellina
42 Route 83 S
North Myrtle Beach, SC 29582
open 7 days a week 4-10
Happy hour served Daily at the Bar 4-7
www.casamorellina.com
casamorellinadine@maildrop.example

Restaurant

Sans Serif

Must have
• Prices and pictures and restaurant information

```html
<!DOCTYPE html>
<html lang="en">
<head>
<meta charset="utf-8">
<title>Casa Morellina — Insalata</title>
<link href="https://fonts.googleapis.com/css2?family=Montserrat:wght@700&family=Questrial&display=swap" rel="stylesheet">
<style>
  :root {
    --tan: #cd8b5e;
    --teal: #3a8574;
    --crimson: #b5174a;
    --white: #ffffff;
    --paper: #f2f3f5;
    --ink: #111111;
    --watermark: #f6dd9c;
  }
  html, body {
    margin: 0;
    padding: 0;
    width: 849px;
    height: 1200px;
    overflow: hidden;
    background: var(--tan);
  }
  .menu-page {
    position: relative;
    width: 849px;
    height: 1200px;
    background: var(--tan);
    font-family: "Questrial", sans-serif;
  }
  .frame {
    position: absolute;
    inset: 0;
  }
  .watermark-name {
    position: absolute;
    left: 107px;
    width: 635px;
    top: 684px;
    text-align: center;
    font-family: "Questrial", sans-serif;
    font-size: 46px;
    line-height: 56px;
    letter-spacing: 2px;
    color: var(--watermark);
    margin: 0;
  }
  .dish-photo {
    position: absolute;
    left: 205px;
    top: 770px;
    width: 440px;
    height: 285px;
  }
  .menu-content {
    position: absolute;
    left: 121px;
    top: 116px;
    width: 607px;
  }
  .section-title {
    font-family: "Montserrat", sans-serif;
    font-weight: 700;
    font-size: 20px;
    line-height: 28px;
    color: var(--teal);
    margin: 0 0 18px;
  }
  .extras {
    margin: 0 0 27px;
    color: var(--teal);
    font-size: 16.5px;
    line-height: 20.5px;
  }
  .extras p { margin: 0; }
  .dish { margin: 0 0 21px; }
  .dish-name {
    color: var(--crimson);
    font-family: "Questrial", sans-serif;
    font-weight: 400;
    font-size: 18.5px;
    line-height: 22px;
    margin: 0;
  }
  .dish-desc {
    margin: 0;
    font-size: 16.5px;
    line-height: 21px;
    color: var(--ink);
  }
  .dish-desc .line {
    display: block;
    white-space: nowrap;
    text-align: justify;
    text-align-last: justify;
  }
  .dish-desc .line.last {
    text-align: left;
    text-align-last: left;
  }
  .dish-price {
    margin: 0;
    font-size: 16.5px;
    line-height: 21px;
    color: var(--ink);
  }
</style>
</head>
<body>
<main class="menu-page">
  <svg class="frame" width="849" height="1200" viewBox="0 0 827 1169" preserveAspectRatio="none" aria-hidden="true">
    <defs>
      <pattern id="tabs-top" patternUnits="userSpaceOnUse" x="104" y="47" width="103.2" height="70">
        <rect x="0" y="0" width="34.4" height="70" rx="17" fill="#3a8574"/>
        <rect x="34.4" y="0" width="34.4" height="70" rx="17" fill="#ffffff"/>
        <rect x="68.8" y="0" width="34.4" height="70" rx="17" fill="#b5174a"/>
      </pattern>
      <pattern id="tabs-bottom" patternUnits="userSpaceOnUse" x="104" y="1058" width="103.2" height="70">
        <rect x="0" y="0" width="34.4" height="70" rx="17" fill="#3a8574"/>
        <rect x="34.4" y="0" width="34.4" height="70" rx="17" fill="#ffffff"/>
        <rect x="68.8" y="0" width="34.4" height="70" rx="17" fill="#b5174a"/>
      </pattern>
      <pattern id="tabs-left" patternUnits="userSpaceOnUse" x="57" y="95" width="70" height="104.7">
        <rect x="0" y="0" width="70" height="34.9" rx="17" fill="#b5174a"/>
        <rect x="0" y="34.9" width="70" height="34.9" rx="17" fill="#ffffff"/>
        <rect x="0" y="69.8" width="70" height="34.9" rx="17" fill="#3a8574"/>
      </pattern>
      <pattern id="tabs-right" patternUnits="userSpaceOnUse" x="700" y="95" width="70" height="104.7">
        <rect x="0" y="0" width="70" height="34.9" rx="17" fill="#3a8574"/>
        <rect x="0" y="34.9" width="70" height="34.9" rx="17" fill="#ffffff"/>
        <rect x="0" y="69.8" width="70" height="34.9" rx="17" fill="#b5174a"/>
      </pattern>
    </defs>
    <rect x="104" y="47" width="619" height="70" fill="url(#tabs-top)"/>
    <rect x="104" y="1058" width="619" height="70" fill="url(#tabs-bottom)"/>
    <rect x="57" y="95" width="70" height="977" fill="url(#tabs-left)"/>
    <rect x="700" y="95" width="70" height="977" fill="url(#tabs-right)"/>
    <rect class="panel" x="104" y="95" width="619" height="985" fill="#f2f3f5"/>
  </svg>

  <p class="watermark-name">Casa Morellina</p>

  <svg class="dish-photo" viewBox="0 0 440 285" role="img" aria-label="Photo of a Greek salad with tomatoes, cucumbers, red onion, olives and feta on a crimson plate">
    <defs>
      <radialGradient id="salad-tones" cx="50%" cy="45%" r="55%">
        <stop offset="0%" stop-color="#c9c4a8"/>
        <stop offset="45%" stop-color="#8c9a5a"/>
        <stop offset="80%" stop-color="#b54a3a"/>
        <stop offset="100%" stop-color="#5e6b3a"/>
      </radialGradient>
    </defs>
    <ellipse cx="205" cy="185" rx="200" ry="92" fill="#b5174a"/>
    <ellipse cx="245" cy="115" rx="182" ry="112" fill="url(#salad-tones)"/>
  </svg>

  <section class="menu-content">
    <h1 class="section-title">INSALATA</h1>
    <div class="extras">
      <p>Add Chicken 3.95</p>
      <p>Add Shrimp 5.95</p>
    </div>

    <article class="dish">
      <h2 class="dish-name">Italian Salad</h2>
      <p class="dish-desc"><span class="line">Fresh Mixed Greens, Tomatoes, Cucumbers, Onions, Mozzarella, Banana</span><span class="line last">Peppers, tossed in our homemade Italian Dressing</span></p>
      <p class="dish-price">8.95</p>
    </article>

    <article class="dish">
      <h2 class="dish-name">Insalata Gorgonzola</h2>
      <p class="dish-desc"><span class="line">Fresh Romaine Lettuce, Gorgonzola, thin sliced Pear, Red Onions, Walnuts,</span><span class="line last">in our homemade Italian Dressing</span></p>
      <p class="dish-price">9.95</p>
    </article>

    <article class="dish">
      <h2 class="dish-name">Greek Salad</h2>
      <p class="dish-desc"><span class="line">Mixed Greens, Tomatoes, Cucumbers, Red Onions, Bell Peppers, Kalama-</span><span class="line last">ta Olives and Feta Cheese in our homemade Italian Dressing</span></p>
      <p class="dish-price">8.95</p>
    </article>

    <article class="dish">
      <h2 class="dish-name">Caesar Salad</h2>
      <p class="dish-desc"><span class="line">Fresh Romaine Tossed with Caesar Dressing, Croutons, topped with Par-</span><span class="line last">mesan Cheese</span></p>
      <p class="dish-price">7.95</p>
    </article>
  </section>
</main>
</body>
</html>
```